RWT Fittings Ltd Business Cards

We need a business card with our business logo. We provide window and door installations on high-rises in west coast British Colombia, Canada.

I would like my business information and details on one side of the card, and the other side the company name with logo

Target Market(s)

General Contractors

Industry/Entity Type

Construction

Contact Information for Business Card

one side i want my company name and logo in the dark theme logo that i provided

Requirements
Must have
• Marco Peltieri, 16045518293, RWTFittings@mailbox-demo.com, 1407-5194 Linden Row Burnaby BC, V5H 2K9, Owner & Manager

```html
<!DOCTYPE html>
<html lang="en">
<head>
<meta charset="utf-8">
<title>RWT Fittings Ltd — Business Cards</title>
<link rel="stylesheet" href="https://fonts.googleapis.com/css2?family=Montserrat:wght@600;700&family=Roboto:wght@400;500&display=swap">
<style>
  :root {
    --page: #252525;
    --card: #202024;
    --blue: #29abe2;
    --grey: #9d9d9d;
    --white: #ffffff;
    --display: "Montserrat", Arial, sans-serif;
    --body: "Roboto", Arial, sans-serif;
  }
  * { box-sizing: border-box; margin: 0; padding: 0; }
  html, body { width: 1200px; height: 780px; overflow: hidden; background: var(--page); }
  .sheet { position: relative; width: 1200px; height: 780px; }
  .card {
    position: absolute; top: 230px; width: 560px; height: 320px;
    background: var(--card); overflow: hidden;
    box-shadow: 0 10px 30px rgba(0,0,0,.45);
  }
  .card--brand { left: 25px; }
  .card--details { left: 615px; }
  .card__bands { position: absolute; inset: 0; }

  /* brand side */
  .brand-mark {
    position: absolute; right: 40px; top: 118px;
    display: flex; align-items: center; gap: 14px;
  }
  .brand-mark__square { width: 26px; height: 26px; background: var(--blue); }
  .brand-mark__name {
    font-family: var(--display); font-weight: 700; font-size: 34px;
    color: var(--grey); letter-spacing: .5px;
  }
  .brand-holder {
    position: absolute; right: 30px; bottom: 22px;
    font-family: var(--display); font-weight: 700; font-size: 27px; color: var(--white);
  }

  /* details side */
  .company {
    position: absolute; left: 34px; top: 40px;
    display: flex; align-items: center; gap: 10px;
  }
  .company__square { width: 20px; height: 20px; background: var(--blue); }
  .company__name {
    font-family: var(--display); font-weight: 700; font-size: 24px; color: var(--blue);
  }
  .holder { position: absolute; right: 44px; top: 102px; text-align: right; }
  .holder__name { font-family: var(--display); font-weight: 700; font-size: 26px; line-height: 1; }
  .holder__first { color: var(--blue); }
  .holder__last { color: var(--grey); }
  .holder__role {
    font-family: var(--body); font-weight: 500; font-size: 13px; color: var(--white);
    margin-top: 5px;
  }
  .divider { position: absolute; left: 40px; right: 150px; top: 168px; height: 1.5px; background: var(--white); }
  .contact {
    position: absolute; left: 40px; top: 184px;
    font-family: var(--body); font-size: 14px; line-height: 1.35; color: var(--white);
  }
  .contact__address { margin-bottom: 12px; }
  .contact__row { display: flex; align-items: center; gap: 8px; }
  .contact__icon { width: 14px; height: 14px; flex: none; }
</style>
</head>
<body>
<main class="sheet">

  <section class="card card--brand" aria-label="Business card, brand side">
    <svg class="card__bands" viewBox="0 0 560 320" aria-hidden="true">
      <polygon points="0,306 330,306 325,320 0,320" fill="var(--grey)"/>
      <polygon points="340,320 362,262 560,262 560,320" fill="var(--blue)"/>
    </svg>
    <div class="brand-mark">
      <span class="brand-mark__square"></span>
      <span class="brand-mark__name">RWT Fittings Ltd</span>
    </div>
    <p class="brand-holder">Marco Peltieri</p>
  </section>

  <section class="card card--details" aria-label="Business card, contact side">
    <svg class="card__bands" viewBox="0 0 560 320" aria-hidden="true">
      <rect x="540" y="96" width="20" height="42" fill="var(--blue)"/>
      <polygon points="0,306 370,306 365,320 0,320" fill="var(--blue)"/>
      <polygon points="378,308 560,308 560,320 374,320" fill="var(--grey)"/>
    </svg>

    <div class="company">
      <span class="company__square"></span>
      <span class="company__name">RWT Fittings Ltd</span>
    </div>

    <div class="holder">
      <p class="holder__name"><span class="holder__first">Marco</span> <span class="holder__last">Peltieri</span></p>
      <p class="holder__role">Owner &amp; Manager</p>
    </div>

    <div class="divider"></div>

    <div class="contact">
      <p class="contact__address">1407-5194 Linden Row<br>Burnaby BC, V5H 2K9</p>
      <p class="contact__row">
        <svg class="contact__icon" viewBox="0 0 24 24" aria-hidden="true"><path fill="var(--blue)" d="M6.6 10.8a15.2 15.2 0 0 0 6.6 6.6l2.2-2.2a1 1 0 0 1 1-.25 11.4 11.4 0 0 0 3.6.57 1 1 0 0 1 1 1V20a1 1 0 0 1-1 1A17 17 0 0 1 3 4a1 1 0 0 1 1-1h3.5a1 1 0 0 1 1 1c0 1.25.2 2.45.57 3.57a1 1 0 0 1-.25 1z"/></svg>
        <span>1604 551 8293</span>
      </p>
      <p class="contact__row">
        <svg class="contact__icon" viewBox="0 0 24 24" aria-hidden="true"><path fill="var(--blue)" d="M3 5h18a1 1 0 0 1 1 1v12a1 1 0 0 1-1 1H3a1 1 0 0 1-1-1V6a1 1 0 0 1 1-1zm1 2.2V17h16V7.2l-8 5.3z M5 7l7 4.6L19 7z"/></svg>
        <span>RWTFittings@mailbox-demo.com</span>
      </p>
    </div>
  </section>

</main>
</body>
</html>
```